High end Electrical/home automation Business Card

Need a card for a high end electrical and home automation company utilising the existing logo.
Phone
Email
Website

Like black look with raised detail. Don’t necessarily need to keep colour of logo it could be made grayscale or white etc

Target Market(s)

High end clients

Contact Information for Business Card

Brightmoor Electrical

Requirements
Must have
• Logo, phone, email, website, address

High end look
Nice to have
• Black background card
Raised font
Should not have
• Lots of colour

```html
<!DOCTYPE html>
<html lang="en">
<head>
<meta charset="utf-8">
<title>Brightmoor Electrical – Business Card</title>
<link href="https://fonts.googleapis.com/css2?family=Archivo:wght@400;700;800&family=Arimo:wght@400&display=swap" rel="stylesheet">
<style>
  :root {
    --backdrop: #c9c9c7;
    --card: #222222;
    --accent: #2494d3;
    --ink: #ffffff;
    --ink-soft: #e6e6e6;
  }
  * { box-sizing: border-box; margin: 0; padding: 0; }
  html, body {
    width: 1200px; height: 801px; overflow: hidden;
    background: var(--backdrop);
  }
  .stage {
    width: 1200px; height: 801px;
    display: flex; align-items: center; justify-content: center; gap: 40px;
  }
  .card {
    position: relative;
    width: 540px; height: 309px;
    background: var(--card);
    border-bottom: 4px solid var(--accent);
    overflow: hidden;
    font-family: "Archivo", Arial, sans-serif;
    color: var(--ink);
  }
  /* Contact side */
  .card-front .emblem {
    position: absolute; top: 46px; right: 40px;
    width: 140px; height: 140px; border-radius: 50%;
    background: var(--accent);
  }
  .card-front .company {
    position: absolute; left: 40px; top: 42px;
    font-weight: 800; font-size: 25px; line-height: 1.1; letter-spacing: -0.3px;
    white-space: nowrap;
  }
  .card-front .person {
    position: absolute; left: 40px; top: 118px;
  }
  .card-front .person-marker {
    position: absolute; left: 0; top: 118px;
    width: 14px; height: 34px; background: var(--accent);
  }
  .person-name {
    font-weight: 800; font-size: 23px; color: var(--accent); line-height: 1;
  }
  .person-title {
    font-family: "Arimo", Arial, sans-serif;
    font-size: 13px; color: var(--ink-soft); margin-top: 3px;
  }
  .contact {
    position: absolute; left: 40px; top: 190px;
    font-family: "Arimo", Arial, sans-serif;
    font-size: 12.5px; line-height: 17px; color: var(--ink-soft);
    list-style: none;
  }
  .contact li { display: flex; align-items: center; gap: 7px; }
  .contact .plain { padding-left: 19px; }
  .contact svg { width: 12px; height: 12px; fill: var(--accent); flex: none; }
  .contact .web-domain { color: var(--accent); }
  /* Logo side */
  .card-back {
    display: flex; align-items: center; justify-content: center; gap: 18px;
  }
  .card-back .emblem {
    width: 46px; height: 46px; border-radius: 50%; background: var(--accent);
    flex: none;
  }
  .card-back .company {
    font-weight: 800; font-size: 36px; letter-spacing: -0.5px; white-space: nowrap;
  }
</style>
</head>
<body>
<main class="stage">
  <section class="card card-front" aria-label="Business card, contact side">
    <div class="emblem"></div>
    <h1 class="company">Brightmoor Electrical</h1>
    <div class="person-marker"></div>
    <div class="person">
      <p class="person-name">Daniel Harrow</p>
      <p class="person-title">Co-Founder</p>
    </div>
    <ul class="contact">
      <li class="plain">410 Alder Crest Rd</li>
      <li class="plain">Suite C Riverton.</li>
      <li>
        <svg viewBox="0 0 24 24" aria-hidden="true"><path d="M6.6 10.8a15.1 15.1 0 0 0 6.6 6.6l2.2-2.2a1 1 0 0 1 1-.25 11.4 11.4 0 0 0 3.6.57 1 1 0 0 1 1 1V20a1 1 0 0 1-1 1A17 17 0 0 1 3 4a1 1 0 0 1 1-1h3.5a1 1 0 0 1 1 1c0 1.250.2 2.45.57 3.57a1 1 0 0 1-.25 1z"/></svg>
        555-210-4872
      </li>
      <li>
        <svg viewBox="0 0 24 24" aria-hidden="true"><path d="M2 5h20v14H2z M2 5l10 8 10-8" /></svg>
        daniel@brightmoorelectrical.com
      </li>
      <li>
        <svg viewBox="0 0 24 24" aria-hidden="true"><circle cx="12" cy="12" r="10"/></svg>
        <span>www.<span class="web-domain">brightmoorelectrical</span>.com</span>
      </li>
    </ul>
  </section>

  <section class="card card-back" aria-label="Business card, logo side">
    <div class="emblem"></div>
    <p class="company">Brightmoor Electrical</p>
  </section>
</main>
</body>
</html>
```